Law Offices business card

Hi there, I'll need business card for the Law Offices of Colin Matheny. The information must convey his strategic approach and quick resolution to complex business litigation needs. Please emphasize Civil Litigation, Corporate Law, Business Governance and Real Estate Law. Colin has over 25 years of experience in these fields.The card should be modern and edgy and the message should be clear. Please consult his current website for ideas.

```html
<!DOCTYPE html>
<html lang="en">
<head>
<meta charset="utf-8">
<title>Law Offices of Colin Matheny – Business Card</title>
<link href="https://fonts.googleapis.com/css2?family=Libre+Baskerville:wght@400;700&family=Open+Sans:wght@400;600;700&display=swap" rel="stylesheet">
<style>
  :root {
    --stage: #2b2b2d;
    --card-dark: #1d1d1d;
    --card-light: #ffffff;
    --lavender: #a7a4c0;
    --lavender-text: #b9b6cf;
    --red: #e2231a;
    --ink: #1a1a1a;
    --muted: #3a3a3a;
  }
  * { margin: 0; padding: 0; box-sizing: border-box; }
  html, body { width: 1200px; height: 900px; overflow: hidden; background: var(--stage); }
  .canvas { position: relative; width: 1200px; height: 900px; }

  .card {
    position: absolute; width: 640px; height: 366px; overflow: hidden;
    box-shadow: 0 14px 30px rgba(0,0,0,.45);
  }
  .card--back { left: 190px; top: 52px; background: var(--card-dark); }
  .card--front { left: 370px; top: 482px; background: var(--card-light); }
  .card-shapes { position: absolute; inset: 0; width: 100%; height: 100%; }

  .firm-name { position: absolute; font-family: "Libre Baskerville", serif; font-weight: 700; line-height: 1; }
  .firm-name__mark { position: absolute; left: 0; top: 6px; width: 14px; height: 14px; background: var(--red); }
  .firm-name__pre { display: block; font-size: 13px; letter-spacing: .08em; text-transform: uppercase; padding-left: 24px; }
  .firm-name__main { display: block; margin-top: 6px; padding-left: 24px; letter-spacing: -.01em; white-space: nowrap; }
  .firm-name__suffix { font-size: .55em; }

  .card--back .firm-name { left: 54px; top: 112px; color: var(--lavender-text); }
  .card--back .firm-name__main { font-size: 40px; }
  .card--front .firm-name { left: 40px; top: 48px; color: var(--ink); }
  .card--front .firm-name__main { font-size: 32px; }

  .services {
    position: absolute; right: 40px; top: 200px; list-style: none; text-align: right;
    font-family: "Open Sans", sans-serif; font-size: 13px; line-height: 1.45;
    letter-spacing: .03em; color: var(--lavender-text); text-transform: uppercase;
  }

  .attorney { position: absolute; right: 44px; top: 44px; text-align: right; font-family: "Open Sans", sans-serif; }
  .attorney__name { font-size: 21px; font-weight: 700; color: var(--ink); letter-spacing: -.01em; }
  .attorney__title { font-size: 11px; font-weight: 600; color: var(--red); letter-spacing: .04em; margin-top: 1px; }

  .address {
    position: absolute; right: 44px; top: 146px; text-align: right; font-style: normal;
    font-family: "Open Sans", sans-serif; font-size: 13px; line-height: 1.35; color: var(--muted);
  }

  .contacts {
    position: absolute; left: 40px; top: 226px; list-style: none;
    font-family: "Open Sans", sans-serif; font-size: 14px; line-height: 1.3; color: var(--ink);
    border-left: 1px solid var(--ink); padding-left: 10px;
  }
  .contacts li { display: flex; align-items: center; gap: 8px; }
  .contacts svg { width: 11px; height: 11px; flex: none; }
</style>
</head>
<body>
<main class="canvas">

  <section class="card card--back" aria-label="Card back">
    <svg class="card-shapes" viewBox="0 0 640 366" aria-hidden="true">
      <polygon points="0,326 400,326 416,334 416,366 0,366" fill="var(--lavender)"/>
      <polygon points="416,326 640,326 640,340 436,340" fill="var(--red)"/>
    </svg>
    <div class="firm-name">
      <span class="firm-name__mark"></span>
      <span class="firm-name__pre">Law Offices of</span>
      <span class="firm-name__main">Colin Matheny<span class="firm-name__suffix">, PA</span></span>
    </div>
    <ul class="services">
      <li>Business Litigation</li>
      <li>Real Estate</li>
      <li>Title and Closing Services</li>
    </ul>
  </section>

  <section class="card card--front" aria-label="Card front">
    <svg class="card-shapes" viewBox="0 0 640 366" aria-hidden="true">
      <rect x="618" y="42" width="22" height="34" fill="var(--red)"/>
      <line x1="40" y1="132" x2="600" y2="132" stroke="var(--ink)" stroke-width="1"/>
      <rect x="440" y="262" width="200" height="36" fill="var(--lavender)"/>
      <rect x="0" y="340" width="440" height="12" fill="var(--red)"/>
    </svg>
    <div class="firm-name">
      <span class="firm-name__mark"></span>
      <span class="firm-name__pre">Law Offices of</span>
      <span class="firm-name__main">Colin Matheny<span class="firm-name__suffix">, PA</span></span>
    </div>
    <div class="attorney">
      <div class="attorney__name">COLIN MATHENY</div>
      <div class="attorney__title">ATTORNEY</div>
    </div>
    <address class="address">
      118B Harbor Avenue<br>Palm Grove, FL 33410
    </address>
    <ul class="contacts">
      <li><svg viewBox="0 0 12 12"><path d="M2 1h3l1 3-2 1a7 7 0 0 0 3 3l1-2 3 1v3c0 1-1 1-1 1C5 11 1 7 1 2c0 0 0-1 1-1z" fill="var(--red)"/></svg>561-555-0142</li>
      <li><svg viewBox="0 0 12 12"><rect x="3" y="0.5" width="6" height="11" rx="1.2" fill="var(--red)"/><rect x="4.2" y="2" width="3.6" height="6.5" fill="#fff"/></svg>561-555-0187</li>
      <li><svg viewBox="0 0 12 12"><rect x="1" y="2.5" width="10" height="7" fill="none" stroke="var(--red)" stroke-width="1.3"/><path d="M1 3l5 4 5-4" fill="none" stroke="var(--red)" stroke-width="1.3"/></svg>colin@mathenylaw.com</li>
      <li><svg viewBox="0 0 12 12"><circle cx="6" cy="6" r="5" fill="none" stroke="var(--red)" stroke-width="1.2"/><ellipse cx="6" cy="6" rx="2.2" ry="5" fill="none" stroke="var(--red)" stroke-width="1"/><line x1="1" y1="6" x2="11" y2="6" stroke="var(--red)" stroke-width="1"/></svg>www.mathenylaw.com</li>
    </ul>
  </section>

</main>
</body>
</html>
```